Business card for law firm

Need business card for new law firm. Think confident, authoritative, conservative, but not stuffy or old-fashioned.

Contact Information for Business Card

Content for card - logo (uploaded), plus the following:

Paul Whitcombe (larger font)
Managing Partner (larger font, but not as large as name)
Level 9, 7 Ferris Lane
Sydney NSW 2000
Main Tel 02 9364 2710
Direct Tel 02 8472 3159
Email paul@qvlegal.com.au
www.qvlegal.com.au

Letterhead design should include logo plus:
Level 9, 7 Ferris Lane
Sydney NSW 2000
Tel 02 8472 3159
www.qvlegal.com.au

```html
<!DOCTYPE html>
<html lang="en">
<head>
<meta charset="utf-8">
<title>Quayvale Legal – Business Card</title>
<link href="https://fonts.googleapis.com/css2?family=Open+Sans:wght@400;600;700&display=swap" rel="stylesheet">
<style>
  :root {
    --navy: #0f1f55;
    --ink: #1c1c1c;
    --grey: #555a61;
    --rule: #cfd2d6;
    --paper: #ffffff;
    --backdrop: #2a2b2d;
  }
  * { box-sizing: border-box; margin: 0; padding: 0; }
  html, body { width: 1200px; height: 960px; overflow: hidden; }
  body {
    background: var(--backdrop);
    font-family: "Open Sans", sans-serif;
    display: flex;
    flex-direction: column;
    align-items: center;
    justify-content: center;
    gap: 56px;
  }
  .card {
    position: relative;
    width: 700px;
    height: 400px;
    background: var(--paper);
    overflow: hidden;
  }

  /* Front */
  .card-front .brand-square {
    position: absolute;
    left: 40px;
    top: 40px;
    width: 190px;
    height: 190px;
    background: var(--navy);
  }
  .card-front .brand-name {
    position: absolute;
    left: 260px;
    top: 150px;
    color: var(--navy);
    font-weight: 600;
    font-size: 46px;
    letter-spacing: 4px;
    line-height: 1.15;
    text-transform: uppercase;
  }
  .card-front .web {
    position: absolute;
    left: 300px;
    top: 300px;
    color: var(--ink);
    font-size: 17px;
    letter-spacing: 3px;
  }

  /* Back */
  .card-back .identity {
    position: absolute;
    left: 40px;
    top: 90px;
    width: 270px;
    display: flex;
    flex-direction: column;
    align-items: center;
    gap: 18px;
  }
  .card-back .brand-square {
    width: 70px;
    height: 70px;
    background: var(--navy);
  }
  .card-back .brand-name {
    color: var(--navy);
    font-weight: 600;
    font-size: 28px;
    letter-spacing: 3px;
    text-transform: uppercase;
    text-align: center;
    line-height: 1.2;
  }
  .card-back .divider {
    position: absolute;
    left: 340px;
    top: 48px;
    width: 1px;
    height: 250px;
    background: var(--rule);
  }
  .card-back .contact {
    position: absolute;
    left: 368px;
    top: 50px;
    color: var(--ink);
    font-size: 17px;
    line-height: 1.5;
  }
  .contact .person {
    color: var(--navy);
    font-weight: 700;
    font-size: 21px;
    text-transform: uppercase;
    line-height: 1.2;
  }
  .contact .role {
    color: var(--grey);
    font-size: 15px;
    text-transform: uppercase;
    margin-bottom: 6px;
  }
  .contact .address { margin-bottom: 4px; }
  .contact .line { display: flex; align-items: center; gap: 8px; }
  .contact .line svg { width: 14px; height: 14px; flex: none; }
  .card-back .band {
    position: absolute;
    left: 0;
    right: 0;
    bottom: 26px;
    height: 14px;
    background: var(--navy);
  }
  .card-back .band-line {
    position: absolute;
    left: 0;
    right: 0;
    bottom: 46px;
    height: 2px;
    background: var(--navy);
  }
</style>
</head>
<body>

  <section class="card card-front">
    <div class="brand-square"></div>
    <div class="brand-name">Quayvale<br>Legal</div>
    <div class="web">www.qvlegal.com.au</div>
  </section>

  <section class="card card-back">
    <div class="identity">
      <div class="brand-square"></div>
      <div class="brand-name">Quayvale<br>Legal</div>
    </div>
    <div class="divider"></div>
    <div class="contact">
      <div class="person">Paul Whitcombe</div>
      <div class="role">Managing Partner</div>
      <div class="address">Level 9, 7 Ferris Lane<br>Sydney NSW 2000</div>
      <div class="line">
        <svg viewBox="0 0 16 16" aria-hidden="true"><circle cx="8" cy="8" r="7.5" fill="var(--navy)"/><path d="M5.2 4.2l1.4-.4 1 2-0.9.8c.4 1 1.2 1.8 2.2 2.2l.8-.9 2 1-.4 1.4c-3 .3-6.4-3.1-6.1-6.1z" fill="#fff"/></svg>
        <span>02 9364 2710(Main)</span>
      </div>
      <div class="line">
        <svg viewBox="0 0 16 16" aria-hidden="true"><circle cx="8" cy="8" r="7.5" fill="var(--navy)"/><path d="M5.2 4.2l1.4-.4 1 2-0.9.8c.4 1 1.2 1.8 2.2 2.2l.8-.9 2 1-.4 1.4c-3 .3-6.4-3.1-6.1-6.1z" fill="#fff"/></svg>
        <span>02 8472 3159(Direct)</span>
      </div>
      <div class="line">
        <svg viewBox="0 0 16 16" aria-hidden="true"><rect x="1" y="3.5" width="14" height="9" rx="1" fill="var(--navy)"/><path d="M1.5 4l6.5 5 6.5-5" fill="none" stroke="#fff" stroke-width="1.2"/></svg>
        <span>paul@qvlegal.com.au</span>
      </div>
      <div class="line">
        <svg viewBox="0 0 16 16" aria-hidden="true"><circle cx="8" cy="8" r="6.8" fill="none" stroke="var(--navy)" stroke-width="1.4"/><ellipse cx="8" cy="8" rx="3" ry="6.8" fill="none" stroke="var(--navy)" stroke-width="1.2"/><path d="M1.5 8h13M2.5 5h11M2.5 11h11" stroke="var(--navy)" stroke-width="1"/></svg>
        <span>www.qvlegal.com.au</span>
      </div>
    </div>
    <div class="band-line"></div>
    <div class="band"></div>
  </section>

</body>
</html>
```